Business card por a urban DJ, up scale audience target

Need a sober design, modern, conservative colors but i can consider some options, y play rnb, hip hop, EDM and top40.

Business card for contact and personal info, double sided, use logo attrached please; im 42 so i need a card acording to my age an target audience.

Target Market(s)

Adult people, up scale audience

Industry/Entity Type

Music Download

Contact Information for Business Card

Cel (318) 4207265518 www.lumadrift.com

Requirements
Must have
• open mind
Nice to have
• open mind
Should not have
• DJ

```html
<!DOCTYPE html>
<html lang="en">
<head>
<meta charset="utf-8">
<title>Lumadrift Business Card</title>
<link rel="stylesheet" href="https://fonts.googleapis.com/css2?family=Jost:wght@400;500;700&display=swap">
<style>
  :root {
    --backdrop: #e9e7e3;
    --card-white: #ffffff;
    --card-black: #151515;
    --ink: #1c1c1c;
    --ink-soft: #6d6d6d;
    --stripe-grey: #9a9a9a;
    --divider: #cfcfcf;
  }
  html, body {
    margin: 0;
    width: 1200px;
    height: 950px;
    overflow: hidden;
    background: var(--backdrop);
    font-family: "Jost", Arial, sans-serif;
  }
  .sheet {
    width: 1200px;
    height: 950px;
    display: flex;
    flex-direction: column;
    align-items: center;
    justify-content: center;
    gap: 50px;
  }
  .card {
    position: relative;
    width: 700px;
    height: 400px;
    box-shadow: 0 6px 18px rgba(0,0,0,0.18);
    overflow: hidden;
  }
  .card--front { background: var(--card-white); }
  .card--back { background: var(--card-black); }
  .card__stripes {
    position: absolute;
    inset: 0;
    width: 700px;
    height: 400px;
  }
  .brand {
    position: absolute;
    left: 70px;
    top: 0;
    width: 300px;
    height: 400px;
    display: flex;
    align-items: center;
    justify-content: center;
  }
  .brand__name {
    font-weight: 700;
    font-size: 84px;
    letter-spacing: 2px;
    color: var(--ink);
  }
  .card__divider {
    position: absolute;
    left: 385px;
    top: 110px;
    width: 1px;
    height: 180px;
    background: var(--divider);
  }
  .contact {
    position: absolute;
    left: 420px;
    top: 128px;
    color: var(--ink);
  }
  .contact__name {
    margin: 0;
    font-weight: 700;
    font-size: 30px;
    letter-spacing: 1px;
    line-height: 1.1;
  }
  .contact__role {
    margin: 4px 0 26px;
    font-weight: 400;
    font-size: 19px;
    letter-spacing: 1px;
    color: var(--ink-soft);
  }
  .contact__line {
    display: flex;
    align-items: center;
    gap: 10px;
    margin: 0 0 10px;
    font-size: 19px;
    font-weight: 500;
    letter-spacing: 0.5px;
  }
  .contact__icon { width: 16px; height: 16px; flex: none; }
</style>
</head>
<body>
<main class="sheet">
  <section class="card card--front" aria-label="Business card front">
    <svg class="card__stripes" viewBox="0 0 700 400" aria-hidden="true">
      <polygon points="60,18 700,18 700,34 44,34" fill="#151515"/>
      <polygon points="30,40 700,40 700,44 26,44" fill="#9a9a9a"/>
      <polygon points="0,356 674,356 670,360 0,360" fill="#9a9a9a"/>
      <polygon points="0,366 656,366 640,382 0,382" fill="#151515"/>
    </svg>

    <div class="brand">
      <span class="brand__name">LUMA</span>
    </div>

    <div class="card__divider"></div>

    <div class="contact">
      <h1 class="contact__name">JOHN SMITH</h1>
      <p class="contact__role">CEO/FOUNDER</p>
      <p class="contact__line">
        <svg class="contact__icon" viewBox="0 0 16 16" aria-hidden="true">
          <rect x="4" y="1" width="8" height="14" rx="1.5" fill="none" stroke="#1c1c1c" stroke-width="1.6"/>
          <line x1="7" y1="12.5" x2="9" y2="12.5" stroke="#1c1c1c" stroke-width="1.4"/>
        </svg>
        (318) 4207265518
      </p>
      <p class="contact__line">
        <svg class="contact__icon" viewBox="0 0 16 16" aria-hidden="true">
          <circle cx="8" cy="8" r="7" fill="#1c1c1c"/>
          <path d="M1 8h14M8 1c2.5 2 2.5 12 0 14M8 1c-2.5 2-2.5 12 0 14" fill="none" stroke="#ffffff" stroke-width="1"/>
        </svg>
        www.lumadrift.com
      </p>
    </div>
  </section>

  <section class="card card--back" aria-label="Business card back"></section>
</main>
</body>
</html>
```